Business Card Design for Marketing Firm

Looking for business card design for higher end marketing firm. Clean but impressionable/trendy. We are a marketing firm that represents manufacturers in the foodservice equipment and supply industry. Our customers are end users such has hotels, restaurants, country clubs, convention centers and casinos as well as distributors of restaurants supplies and equipment, and manufacturers of foodservice equipment and supplies.
Target Market(s)
Hotels, Restaurants, Supply & Equipment Distributors, Foodservice Manufacturers
Industry/Entity Type
Foodservice/Hospitality
Contact Information for Business Card
Name, Title, Contact Number, Email, Website, Social Media, Address
Requirements
Must have
- Clean & Simple but Serious and Impressionable

```html
<!DOCTYPE html>
<html lang="en">
<head>
<meta charset="utf-8">
<title>Meridian Service Reps – Business Card</title>
<link rel="stylesheet" href="https://fonts.googleapis.com/css2?family=Montserrat:wght@400;500;700&display=swap">
<style>
  :root {
    --navy: #24266a;
    --navy-soft: #6a6b9e;
    --paper: #ffffff;
    --paper-grey: #ececec;
    --ink: #4a4a4a;
    --backdrop: #d4d4d4;
  }
  * { margin: 0; padding: 0; box-sizing: border-box; }
  html, body { width: 1200px; height: 1200px; overflow: hidden; }
  body {
    background: var(--backdrop);
    font-family: "Montserrat", sans-serif;
    position: relative;
  }
  .card {
    position: absolute;
    left: 180px;
    width: 840px;
    height: 480px;
    border-radius: 28px;
    overflow: hidden;
    background: var(--paper);
    box-shadow: 0 8px 20px rgba(0,0,0,0.18);
  }
  .card-front { top: 60px; }
  .card-back { top: 600px; background: var(--paper-grey); }

  /* front */
  .front-brand {
    position: absolute;
    left: 0; right: 0; top: 150px;
    text-align: center;
    color: var(--navy);
    font-weight: 500;
  }
  .front-brand .brand-mark {
    display: inline-block;
    width: 90px; height: 90px;
    border-radius: 50%;
    background: var(--navy);
    margin-bottom: 22px;
  }
  .front-brand .brand-name {
    display: block;
    font-size: 40px;
    letter-spacing: 3px;
  }
  .social {
    position: absolute;
    left: 0; right: 0; bottom: 70px;
    display: flex; justify-content: center; align-items: center; gap: 12px;
    color: var(--ink);
    font-size: 20px;
  }
  .social-dot {
    width: 22px; height: 22px; border-radius: 50%; background: var(--navy);
  }

  /* back */
  .back-art { position: absolute; inset: 0; }
  .person {
    position: absolute; left: 60px; top: 96px; color: var(--paper);
  }
  .person-name { font-size: 40px; font-weight: 700; }
  .person-title { font-size: 21px; font-weight: 400; margin-top: 6px; }
  .back-brand {
    position: absolute; right: 60px; top: 70px;
    text-align: right; color: var(--paper); font-weight: 500;
  }
  .back-brand .brand-mark {
    display: inline-block; width: 46px; height: 46px; border-radius: 50%;
    background: var(--paper); margin-bottom: 12px;
  }
  .back-brand .brand-name { display: block; font-size: 22px; letter-spacing: 2px; }
  .address {
    position: absolute; left: 60px; top: 285px;
    color: var(--ink); font-size: 21px; line-height: 1.3;
  }
  .contacts {
    position: absolute; left: 60px; top: 360px;
    list-style: none; color: var(--ink); font-size: 21px;
  }
  .contacts li { display: flex; align-items: center; gap: 12px; line-height: 1.5; }
  .contacts svg { width: 20px; height: 20px; fill: var(--navy); flex: none; }
</style>
</head>
<body>

<section class="card card-front">
  <div class="front-brand">
    <span class="brand-mark"></span>
    <span class="brand-name">MERIDIAN SERVICE REPS</span>
  </div>
  <div class="social">
    <span class="social-dot"></span>
    <span>@meridianservicereps</span>
  </div>
</section>

<section class="card card-back">
  <svg class="back-art" viewBox="0 0 840 480" preserveAspectRatio="none">
    <defs>
      <linearGradient id="bandGradient" x1="0" y1="0" x2="1" y2="0">
        <stop offset="0" stop-color="var(--navy-soft)"/>
        <stop offset="0.45" stop-color="var(--navy)"/>
        <stop offset="1" stop-color="var(--navy)"/>
      </linearGradient>
    </defs>
    <path d="M0 0 H840 V250 C800 360 700 380 600 372 C460 260 300 205 190 205 C110 205 40 215 0 225 Z" fill="url(#bandGradient)"/>
    <path d="M190 205 C380 195 560 270 740 480 L720 480 C550 290 380 220 190 205 Z" fill="var(--navy)"/>
    <path d="M600 372 C660 400 720 440 770 480 L755 480 C710 445 655 405 600 372 Z" fill="var(--navy)"/>
  </svg>

  <div class="person">
    <div class="person-name">Daniel Crane</div>
    <div class="person-title">Founder &amp; Director</div>
  </div>

  <div class="back-brand">
    <span class="brand-mark"></span>
    <span class="brand-name">MERIDIAN SERVICE REPS</span>
  </div>

  <div class="address">
    4470 Harbor Lane<br>Westbrook Maine 04092
  </div>

  <ul class="contacts">
    <li>
      <svg viewBox="0 0 24 24"><path d="M6.6 10.8a15 15 0 0 0 6.6 6.6l2.2-2.2c.3-.3.7-.4 1-.2 1.1.4 2.3.6 3.6.6.6 0 1 .4 1 1V20c0 .6-.4 1-1 1A17 17 0 0 1 3 4c0-.6.4-1 1-1h3.5c.6 0 1 .4 1 1 0 1.3.2 2.5.6 3.6.1.3 0 .7-.2 1z"/></svg>
      (555)-014-2290
    </li>
    <li>
      <svg viewBox="0 0 24 24"><path d="M2 5h20v14H2z M2 5l10 8 10-8" fill="var(--navy)"/><path d="M3 6l9 7 9-7" stroke="#fff" stroke-width="1.5" fill="none"/></svg>
      crane@meridianservicereps.com
    </li>
    <li>
      <svg viewBox="0 0 24 24"><circle cx="12" cy="12" r="10"/><path d="M2 12h20M12 2c3 3 3 17 0 20M12 2c-3 3-3 17 0 20" stroke="#fff" stroke-width="1.3" fill="none"/></svg>
      www.meridianservicereps.com
    </li>
  </ul>
</section>

</body>
</html>
```